New Business Card Design Project

We would like a business card that represents the sale of boat, home, auto, and life insurance.

The logo can change colors to meet the look of the design if needed.

Industry/Entity Type

Business

```html
<!DOCTYPE html>
<html lang="en">
<head>
<meta charset="utf-8">
<title>Larkstone Financial – Business Card</title>
<link rel="stylesheet" href="https://fonts.googleapis.com/css2?family=Jost:wght@400&family=Open+Sans:wght@400;700&display=swap">
<style>
  :root {
    --backdrop: #3b3330;
    --card: #f4f4f4;
    --ink: #4a4a4c;
    --teal: #356c82;
    --slate: #4b4b4d;
    --white: #ffffff;
  }
  * { box-sizing: border-box; margin: 0; padding: 0; }
  html, body { width: 1200px; height: 768px; overflow: hidden; }
  body {
    background: var(--backdrop);
    font-family: "Open Sans", Arial, sans-serif;
    position: relative;
  }
  .card {
    position: absolute;
    top: 236px;
    width: 520px;
    height: 296px;
    background: var(--card);
    overflow: hidden;
    box-shadow: 0 6px 18px rgba(0,0,0,.35);
  }
  .card--front { left: 45px; }
  .card--back { left: 635px; }

  .brand {
    display: flex;
    align-items: center;
    gap: 10px;
    position: absolute;
  }
  .brand__dot {
    width: 22px; height: 22px;
    border-radius: 50%;
    background: var(--teal);
    flex: none;
  }
  .brand__name {
    font-family: "Jost", "Futura", sans-serif;
    font-weight: 400;
    color: var(--ink);
    letter-spacing: 3px;
    white-space: nowrap;
  }
  .card--front .brand { left: 50%; top: 50%; transform: translate(-50%, -50%); }
  .card--front .brand__name { font-size: 30px; }

  .card--back .brand { right: 28px; top: 118px; }
  .card--back .brand__name { font-size: 24px; letter-spacing: 2.5px; }

  .services {
    position: absolute;
    left: 24px; top: 20px;
    font-size: 13px;
    color: #222;
    line-height: 1.35;
  }
  .services__title { font-weight: 700; }
  .services ul { list-style: none; padding-left: 6px; }
  .services li::before { content: "»"; color: var(--teal); margin-right: 8px; }

  .contact-band {
    position: absolute;
    left: 0; bottom: 0;
    width: 318px; height: 120px;
    background: var(--teal);
    color: var(--white);
    font-size: 13px;
    padding: 18px 0 0 24px;
    line-height: 1.55;
  }
  .contact-row { display: flex; align-items: center; gap: 7px; white-space: nowrap; }
  .contact-row svg { width: 12px; height: 12px; flex: none; }
  .contact-row .gap { margin-left: 12px; }

  .web-band {
    position: absolute;
    right: 0; bottom: 0;
    width: 202px; height: 56px;
    background: var(--slate);
    color: var(--white);
    font-size: 14px;
    display: flex; align-items: center; justify-content: center;
  }
</style>
</head>
<body>

<section class="card card--front" aria-label="Card front">
  <div class="brand">
    <span class="brand__dot"></span>
    <span class="brand__name">LARKSTONE FINANCIAL</span>
  </div>
</section>

<section class="card card--back" aria-label="Card back">
  <div class="services">
    <p class="services__title">Sale of :</p>
    <ul>
      <li>Boat Insurance</li>
      <li>Home Insurance</li>
      <li>Auto Insurance</li>
      <li>Life Insurance.</li>
    </ul>
  </div>

  <div class="brand">
    <span class="brand__dot"></span>
    <span class="brand__name">LARKSTONE FINANCIAL</span>
  </div>

  <div class="contact-band">
    <p class="contact-row">
      <svg viewBox="0 0 12 12" fill="#fff" aria-hidden="true"><path d="M1 4c0-2 1-3 2-3h6c1 0 2 1 2 3l-2 1-1-1H4L3 5 1 4zM3 6h6l1 5H2z"/></svg>
      0000 0000 00
      <svg class="gap" viewBox="0 0 12 12" fill="#fff" aria-hidden="true"><rect x="3" y="0.5" width="6" height="11" rx="1"/><rect x="4" y="2" width="4" height="7" fill="#356c82"/></svg>
      0000 0000 0000
    </p>
    <p class="contact-row">
      <svg viewBox="0 0 12 12" fill="none" stroke="#fff" stroke-width="1.2" aria-hidden="true"><circle cx="6" cy="6" r="5"/><ellipse cx="6" cy="6" rx="2.2" ry="5"/><path d="M1 6h10"/></svg>
      yourname@yourwebsite.com
    </p>
    <p class="contact-row">
      <svg viewBox="0 0 12 12" aria-hidden="true"><rect x="0.5" y="2" width="11" height="8" fill="#fff"/><path d="M0.5 2l5.5 4.5L11.5 2" fill="none" stroke="#356c82" stroke-width="1.2"/></svg>
      your official or residential address
    </p>
  </div>

  <div class="web-band">www.yourwebsite.com</div>
</section>

</body>
</html>
```